Fitness Equipment & Service

I want to make the card eye catching and fun. We are called Corvane Motion Limited and we are based in Wales. We sell, install and service all types of fitness equipment from Skipping ropes, right through the Dumbbells, Kettle bells and Barbells through to state of the art Treadmills, Running Machines and Strength Equipment. We also design and install changing room furniture and lockers.

TYPOGRAPHY
We would like to use Futrura. Futura has an appearance of efficiency and forwardness. The typeface is derived
from simple geometric forms (near-perfect circles, triangles and squares) and is based on strokes of
near-even weight, which are low in contrast. This is most visible in the almost perfectly round stroke of
the o, which is nonetheless slightly ovoid.
The lowercase has tall ascenders, which rise above the cap line. The uppercase
characters present proportions similar to those of classical Roman capitals.

TYPOGRAPHIC CONSIDERATIONS
No Strike though
No Horizontal Scaling
No Drop Shadows
No Effects
Never use less than 120% Leading

OUR CORPORATE COLOURS
BRAND GUIDELINES
We were thinking that our primary colour palette consists of the Acid Green (Pantone 382) and Process Black.

We work closely with tquarly Ltd and would like to include their name on the card somewhere. I have attached images of the other brands that we work with as an idea or the small icons I have included that illustrate what we do?. I have very kindly been given permission to use any of the images off the files that I have included below, so I hope these help. I will include these below. I would be open to suggestions if it made the card more striking Can you do it?
Updates

Hi All, Just wanted to add a few thoughts but you are the guys with the creative visions (thats why are here) We are based in Wales, UK and we would be open to lots of different ideas on a theme but must be eye catching, Bold and FUN. If you can or think that the Welsh or any dragon could be put in there then go for it (its not a must have) We have also added some ideas for colour but again its over to you!! GO FOR IT ! Thanks and look forward to your visions! Owen

Hi All, Just thought I would sen through the contact details that need to be on the card. (if you want to play around with icons instead of the wording twitter, Facebook, go for it): Corvane Motion Limited Owen Pritchard Managing Director Mob: +44 (0)7582 913 406 e-mail: sales@corvanemotion.co.uk Web: Corvanemotion.co.uk twitter: @motionLetterbin Facebook: Corvane Motion Limited

```html
<!DOCTYPE html>
<html lang="en">
<head>
<meta charset="utf-8">
<title>Corvane Motion Limited – Business Card</title>
<link rel="stylesheet" href="https://fonts.googleapis.com/css2?family=Libre+Franklin:wght@400;600&display=swap">
<style>
  :root {
    --page-bg: #e9e7e2;
    --card-white: #ffffff;
    --card-shade: #dcdcdc;
    --navy: #1f2a5c;
    --globe-blue: #263a8a;
    --gold: #b8902f;
    --ink: #3b3b3b;
    --icon-grey: #4a4a4a;
  }
  * { box-sizing: border-box; margin: 0; padding: 0; }
  html, body { width: 1200px; height: 950px; overflow: hidden; }
  body {
    background: var(--page-bg);
    font-family: "Libre Franklin", Arial, sans-serif;
    display: flex;
    flex-direction: column;
    align-items: center;
    justify-content: center;
    gap: 40px;
  }
  .card {
    width: 740px;
    height: 423px;
    position: relative;
    background: linear-gradient(120deg, var(--card-white) 40%, var(--card-shade));
    box-shadow: 0 6px 18px rgba(0,0,0,0.18);
    overflow: hidden;
  }

  /* Back */
  .card-back .back-mark {
    position: absolute;
    left: 50%;
    top: 70px;
    transform: translateX(-50%);
    display: flex;
    flex-direction: column;
    align-items: center;
    gap: 18px;
  }
  .mark-circle {
    border-radius: 50%;
    background: radial-gradient(circle at 40% 35%, #3350a8, var(--globe-blue) 55%, #14205a);
  }
  .card-back .mark-circle { width: 150px; height: 150px; }
  .company-name {
    color: var(--navy);
    font-weight: 600;
    text-transform: uppercase;
    letter-spacing: 0.04em;
  }
  .card-back .company-name { font-size: 20px; }
  .card-back .back-web {
    position: absolute;
    right: 48px;
    bottom: 40px;
    font-size: 17px;
    color: var(--ink);
    letter-spacing: 0.02em;
  }

  /* Front */
  .card-front .front-mark {
    position: absolute;
    left: 45px;
    top: 55px;
    width: 300px;
    height: 300px;
  }
  .card-front .front-mark.mark-circle { box-shadow: 0 0 0 6px #f1f1f1, 0 0 0 8px #cfcfcf; }
  .contact {
    position: absolute;
    right: 40px;
    top: 40px;
    text-align: right;
    line-height: 1.3;
  }
  .card-front .company-name { font-size: 21px; margin-bottom: 32px; }
  .person-name { color: var(--navy); font-size: 21px; font-weight: 600; }
  .person-role { color: var(--gold); font-size: 17px; margin-bottom: 4px; }
  .contact-list { list-style: none; font-size: 17px; color: var(--ink); }
  .contact-list li { display: flex; justify-content: flex-end; align-items: center; gap: 10px; height: 24px; }
  .contact-list .no-icon { padding-right: 28px; }
  .icon { width: 18px; height: 18px; flex: none; }
</style>
</head>
<body>

  <section class="card card-back">
    <div class="back-mark">
      <div class="mark-circle" role="img" aria-label="Company emblem area"></div>
      <span class="company-name">Corvane Motion Limited</span>
    </div>
    <span class="back-web">corvanemotion.co.uk</span>
  </section>

  <section class="card card-front">
    <div class="front-mark mark-circle" role="img" aria-label="Company emblem area"></div>
    <div class="contact">
      <p class="company-name">Corvane Motion Limited</p>
      <p class="person-name">Owen Pritchard</p>
      <p class="person-role">Managing Director</p>
      <ul class="contact-list">
        <li class="no-icon">6172 Lindenmere Drive</li>
        <li class="no-icon">Pennard Vale, CF 11002</li>
        <li class="no-icon">sales@corvanemotion.co.uk</li>
        <li>+44 (0)7582 913 406
          <svg class="icon" viewBox="0 0 18 18" aria-hidden="true"><rect x="4" y="1" width="10" height="16" rx="2" fill="var(--icon-grey)"/><rect x="6" y="3" width="6" height="10" fill="#fff"/></svg>
        </li>
        <li>Corvanemotion.co.uk
          <svg class="icon" viewBox="0 0 18 18" aria-hidden="true"><rect x="1" y="4" width="16" height="11" rx="1.5" fill="var(--icon-grey)"/><path d="M2 5 L9 11 L16 5" stroke="#fff" stroke-width="1.4" fill="none"/></svg>
        </li>
        <li>@motionLetterbin
          <svg class="icon" viewBox="0 0 18 18" aria-hidden="true"><circle cx="9" cy="9" r="8" fill="var(--icon-grey)"/></svg>
        </li>
        <li>Corvane Motion Limited
          <svg class="icon" viewBox="0 0 18 18" aria-hidden="true"><rect x="1.5" y="1.5" width="15" height="15" rx="2" fill="var(--icon-grey)"/></svg>
        </li>
        <li class="no-icon"></li>
      </ul>
    </div>
  </section>

</body>
</html>
```